Web Developer Needs a Business Card Design

I need a personal business card design that represents me as a web developer for potential employers. I would like the background to be a dark color on the front for contrast with my logo and name. The back will have all my information along with a smaller version of the logo. I want something with a modern look and feel, not too conservative. This will be used for potential employers and freelance work.

Industry/Entity Type

Business

Contact Information for Business Card

Front should have my logo and name. The back should have all my personal information which would include: name: Tom Varulek, phone: 570-614-3098, email: tomvarulek@quillbox.net, website url: www.tomvarulek.net, logo, web developer.

Font styles to use
Sans Serif

Requirements
Must have
• Must include my logo. The color palette base color will be the logo color.

```html
<!DOCTYPE html>
<html lang="en">
<head>
<meta charset="utf-8">
<title>Tom Varulek — Business Card</title>
<link rel="stylesheet" href="https://fonts.googleapis.com/css2?family=Arimo:wght@400;700&display=swap">
<style>
  :root {
    --canvas-bg: #e9e6e1;
    --card-black: #0d0d0d;
    --card-white: #ffffff;
    --teal: #6fcdb8;
    --teal-light: #a6ddd1;
    --ink: #111111;
    --shadow: rgba(0,0,0,0.18);
  }
  * { margin: 0; padding: 0; box-sizing: border-box; }
  html, body {
    width: 1200px; height: 892px; overflow: hidden;
    background: var(--canvas-bg);
    font-family: "Arimo", Arial, sans-serif;
  }
  .sheet {
    position: relative; width: 1200px; height: 892px;
    display: flex; align-items: center; justify-content: center; gap: 40px;
  }
  .card {
    position: relative; width: 540px; height: 309px;
    box-shadow: 0 10px 28px var(--shadow);
    overflow: hidden;
  }
  .card--front { background: var(--card-black); }
  .card--back { background: var(--card-white); }

  .front-mark {
    position: absolute; left: 190px; top: 28px;
    width: 160px; height: 160px; border-radius: 50%;
    border: 11px solid var(--teal);
    display: flex; align-items: center; justify-content: center;
  }
  .mark-name {
    color: var(--teal); font-size: 26px; font-weight: 700;
  }
  .front-name {
    position: absolute; left: 0; right: 0; top: 214px;
    text-align: center; color: var(--card-white);
    font-size: 44px; font-weight: 400; letter-spacing: 2px;
  }

  .back-art { position: absolute; inset: 0; }
  .back-mark {
    position: absolute; left: 112px; top: 88px;
    width: 124px; height: 124px; border-radius: 50%;
    background: var(--card-black);
    border: 6px solid var(--card-white);
    box-shadow: 0 0 0 5px var(--card-black);
    display: flex; align-items: center; justify-content: center;
  }
  .back-mark .mark-name { font-size: 22px; }
  .identity {
    position: absolute; right: 26px; top: 100px; text-align: right; color: var(--ink);
  }
  .identity__name { font-size: 31px; font-weight: 400; line-height: 1.1; }
  .identity__role { font-size: 15px; margin-top: 2px; }
  .contacts {
    position: absolute; right: 26px; top: 196px;
    list-style: none; color: var(--ink); font-size: 16px;
  }
  .contacts li {
    display: flex; align-items: center; justify-content: flex-end;
    gap: 8px; height: 24px;
  }
  .contact-icon { width: 13px; height: 13px; display: block; }
</style>
</head>
<body>
<main class="sheet">
  <section class="card card--front" aria-label="Card front">
    <div class="front-mark"><span class="mark-name">varulek</span></div>
    <h1 class="front-name">TOM VARULEK</h1>
  </section>

  <section class="card card--back" aria-label="Card back">
    <svg class="back-art" viewBox="0 0 540 309" width="540" height="309" aria-hidden="true">
      <defs>
        <linearGradient id="tealBand" x1="0" y1="0" x2="1" y2="1">
          <stop offset="0" stop-color="var(--teal)"/>
          <stop offset="1" stop-color="var(--teal-light)"/>
        </linearGradient>
      </defs>
      <path d="M0 0 H395 C330 120 170 225 0 262 Z" fill="url(#tealBand)"/>
      <path d="M395 0 C330 120 170 225 0 262" fill="none" stroke="var(--card-black)" stroke-width="5"/>
    </svg>
    <div class="back-mark"><span class="mark-name">varulek</span></div>

    <div class="identity">
      <div class="identity__name">Tom Varulek</div>
      <div class="identity__role">web developer</div>
    </div>

    <ul class="contacts">
      <li>570-614-3098
        <svg class="contact-icon" viewBox="0 0 13 13"><rect width="13" height="13" fill="var(--ink)"/><path d="M4 3 Q3 7 8 10 L9.5 8.8 L8 7.6 L7 8.2 Q5.3 7 4.9 5.3 L5.8 4.6 L5 3 Z" fill="#fff"/></svg>
      </li>
      <li>tomvarulek@quillbox.net
        <svg class="contact-icon" viewBox="0 0 13 13"><rect width="13" height="13" fill="var(--ink)"/><rect x="2.5" y="3.8" width="8" height="5.6" fill="none" stroke="#fff" stroke-width="1"/><path d="M2.5 3.8 L6.5 7 L10.5 3.8" fill="none" stroke="#fff" stroke-width="1"/></svg>
      </li>
      <li>www.tomvarulek.net
        <svg class="contact-icon" viewBox="0 0 13 13"><rect width="13" height="13" fill="var(--ink)"/><circle cx="6.5" cy="6.5" r="3.8" fill="none" stroke="#fff" stroke-width="1"/><path d="M2.7 6.5 H10.3 M6.5 2.7 Q4.5 6.5 6.5 10.3 M6.5 2.7 Q8.5 6.5 6.5 10.3" fill="none" stroke="#fff" stroke-width="0.8"/></svg>
      </li>
    </ul>
  </section>
</main>
</body>
</html>
```